'Little Lantern' promotional brochure

We have designed a 6 week program to educate impending first-time parents about the things they need to know to survive the first 6 months. Sessions delivered by general practitioner/family doctor, dietician, physiotherapist, speech pathologist and psychologist. Our promotional blurb is: 'A comprehensive education program for first-time parents-to-be, delivered over 6 weeks by health professionals in your community, about everything you need to know to look after your baby (and yourself!) in the first 6 months'. I now want to put together a promotional brochure to be distributed to those couples who express an interest which will provide further details of what will be delivered in the course.
Updates
In terms of layout, I envisaged a double sided A4 size, foldable into 3 sections, but very happy to be guided on this.
Target Market(s)
To appeal to a young, well educated demographic. First time parents couples.
Industry/Entity Type
Medical
Font styles to use
Other font styles liked:
- Playfair Display
Requirements
Must have
- Playfair display font to be consistent with our logo (attached). Logo also included please. Some consistency with colours of logo please.
Nice to have
- I am a doctor, and have no creative genes! But prefer a clean and professional appearance overall. Not too cluttered in overall appearance.
Should not have
- No cheesy pictures of babies.

```html
<!DOCTYPE html>
<html lang="en">
<head>
<meta charset="utf-8">
<title>Little Lantern brochure</title>
<link rel="stylesheet" href="https://fonts.googleapis.com/css2?family=Playfair+Display:wght@400;500&family=Raleway:wght@300;400&display=swap">
<style>
:root{
  --bg:#d6d7d9;
  --green:#6cbd45;
  --green-dark:#4f9a2f;
  --grey:#7b7b7b;
  --ink:#333;
  --ink-soft:#555;
  --paper:#fff;
  --serif:"Playfair Display", Georgia, serif;
  --sans:"Raleway", Helvetica, Arial, sans-serif;
}
*{box-sizing:border-box;margin:0;padding:0}
h1,h2,h3{font-weight:400}
html,body{width:892px;height:1200px;overflow:hidden;background:var(--bg)}
.canvas{position:relative;width:892px;height:1200px}
.spread{position:absolute;left:98px;width:676px;height:477px;background:var(--paper);overflow:hidden}
.spread--outside{top:100px}
.spread--inside{top:633px}
.spread > svg{position:absolute;left:0;top:0}
.abs{position:absolute}

.brand{display:flex;align-items:center;gap:8px}
.brand__dot{width:30px;height:30px;border-radius:50%;background:var(--green);flex:none}
.brand__name{font-family:var(--serif);font-weight:400;color:var(--green);font-size:13px;line-height:14px;letter-spacing:.4px;text-transform:uppercase}

.intro{left:0;width:225px;text-align:center;font-family:var(--serif);color:var(--ink)}
.intro__title{font-size:23px;color:var(--green);letter-spacing:.5px;line-height:1;white-space:nowrap}
.intro__lead{font-size:9.5px;line-height:13px;text-transform:uppercase}
.intro__text{font-size:10px;line-height:12.5px;color:var(--ink-soft)}
.intro__cost{font-size:10px;color:var(--green-dark);text-transform:uppercase}

.contact{left:225px;width:226px;text-align:center;color:#fff}
.contact__head{font-family:var(--serif);font-size:12px;line-height:16px;text-transform:uppercase;letter-spacing:.3px}
.contact__rule{width:150px;height:1px;margin:6px auto 0;border-top:1px dotted rgba(255,255,255,.5)}
.contact__org{font-family:var(--serif);font-size:9.5px;line-height:13px;text-transform:uppercase}
.contact__line{font-family:var(--sans);font-size:8px;line-height:11.5px}
.contact__phone{font-family:var(--sans);font-size:10px}
.contact__web{font-family:var(--sans);font-size:9px}

.cover-title{left:451px;width:225px;text-align:center;font-family:var(--serif);color:#fff;font-size:22px;letter-spacing:.5px;white-space:nowrap}

.inside-title{left:225px;width:226px;text-align:center;font-family:var(--serif);font-size:22px;line-height:1;color:#e2e2e2;letter-spacing:.3px;white-space:nowrap}
.col{top:158px;width:193px;font-family:var(--sans);font-weight:300;font-size:6.9px;line-height:9.7px;color:var(--ink-soft)}
.col--1{left:19px}
.col--2{left:243px}
.col--3{left:464px}
.week{margin-bottom:9px}
.week__title{font-family:var(--serif);font-size:11px;color:var(--green);text-transform:uppercase;padding-bottom:3px;border-bottom:1px dotted #cfcfcf;margin-bottom:7px}
.week p{text-align:justify;margin-bottom:7px}
.session{color:var(--green-dark)}
.bullets{list-style:none;margin-bottom:3px}
.bullets li{padding-left:8px;position:relative;line-height:11.5px;white-space:nowrap}
.bullets li::before{content:"";position:absolute;left:0;top:4px;width:4px;height:4px;border-radius:50%;background:#bbb}
.bullets--split{display:grid;grid-template-columns:78px 1fr;column-gap:4px}
</style>
</head>
<body>
<div class="canvas">

  <section class="spread spread--outside">
    <svg width="676" height="477" viewBox="0 0 676 477">
      <defs>
        <linearGradient id="paperFade" x1="0" y1="0" x2="1" y2="0">
          <stop offset="0" stop-color="#f4f4f4"/><stop offset="1" stop-color="#ffffff"/>
        </linearGradient>
        <linearGradient id="photoGrey" x1="0" y1="0" x2="1" y2="1">
          <stop offset="0" stop-color="#d9d9d9"/><stop offset="1" stop-color="#9a9a9a"/>
        </linearGradient>
        <linearGradient id="photoWarm" x1="0" y1="0" x2="1" y2="1">
          <stop offset="0" stop-color="#e6e6e6"/><stop offset=".6" stop-color="#b4b4b4"/><stop offset="1" stop-color="#d0d0d0"/>
        </linearGradient>
      </defs>
      <rect x="0" y="0" width="225" height="477" fill="url(#paperFade)"/>
      <rect x="451" y="0" width="225" height="477" fill="url(#paperFade)"/>
      <rect x="225" y="0" width="226" height="477" fill="var(--grey)"/>
      <circle cx="300" cy="-20" r="80" fill="none" stroke="#c9c9c9" stroke-width=".8"/>

      <path d="M0,412 Q110,360 225,356 L225,477 L0,477Z" fill="url(#photoGrey)" role="img" aria-label="Black and white photo of parents' hands cradling a baby's feet"/>
      <path d="M0,412 Q110,360 225,356" fill="none" stroke="var(--green)" stroke-width="3"/>

      <path d="M225,356 Q340,350 451,392 L451,477 L225,477Z" fill="var(--green)"/>
      <circle cx="338" cy="323" r="88" fill="none" stroke="rgba(255,255,255,.35)" stroke-width="1"/>
      <circle cx="338" cy="323" r="70" fill="#8a8a8a"/>
      <circle cx="338" cy="323" r="64" fill="#e4e4e4" role="img" aria-label="Street map showing the clinic location"/>

      <path d="M451,135 Q560,140 676,105 L676,132 Q560,160 451,153Z" fill="var(--green)"/>
      <path d="M451,153 Q560,160 676,132 L676,380 Q560,410 451,398Z" fill="url(#photoWarm)" role="img" aria-label="Black and white photo of a mother holding her baby close"/>
      <path d="M451,398 Q560,410 676,380 L676,477 L451,477Z" fill="var(--green)"/>
      <path d="M451,398 Q560,410 676,380" fill="none" stroke="#fff" stroke-width="2"/>
    </svg>

    <div class="abs brand" style="left:42px;top:52px">
      <span class="brand__dot"></span>
      <span class="brand__name">Wattlebrook<br>Health &amp;<br>Medical</span>
    </div>

    <div class="abs intro" style="top:172px">
      <h1 class="intro__title">LITTLE LANTERN</h1>
      <p class="intro__lead" style="margin-top:14px">A comprehensive education<br>program for first-time parents.</p>
      <p class="intro__text" style="margin-top:13px">Delivered over 6 weeks by health<br>professionals in your community.</p>
      <p class="intro__text" style="margin-top:12px">Everything you need to know to look after<br>your baby (and yourself!)<br>in the first 6 months</p>
      <p class="intro__cost" style="margin-top:16px">Total cost $300</p>
    </div>

    <div class="abs contact" style="top:40px">
      <h2 class="contact__head">Contact details for<br>enquiries bookings</h2>
      <div class="contact__rule"></div>
      <p class="contact__org" style="margin-top:12px">Wattlebrook<br>Health &amp; Medical</p>
      <p class="contact__line" style="margin-top:9px">Banksia Shopping Village, Shop 11<br>214 Banksia Way<br>Wattlebrook NSW 2490</p>
      <p class="contact__phone" style="margin-top:12px">02 5550 0148</p>
      <p class="contact__line" style="margin-top:12px">reception@wattlebrookhealth.com.au</p>
    </div>
    <p class="abs contact contact__web" style="top:445px">www.wattlebrookhealth.com.au</p>

    <div class="abs brand" style="left:474px;top:40px">
      <span class="brand__dot" style="width:36px;height:36px"></span>
      <span class="brand__name" style="font-size:16px;line-height:17px">Wattlebrook<br>Health &amp;<br>Medical</span>
    </div>
    <p class="abs cover-title" style="top:424px">LITTLE LANTERN</p>
  </section>

  <section class="spread spread--inside">
    <svg width="676" height="477" viewBox="0 0 676 477">
      <defs>
        <linearGradient id="photoSoft" x1="0" y1="0" x2="1" y2="1">
          <stop offset="0" stop-color="#e8e8e8"/><stop offset="1" stop-color="#a8a8a8"/>
        </linearGradient>
        <linearGradient id="colFade" x1="0" y1="0" x2="1" y2="0">
          <stop offset="0" stop-color="#ececec"/><stop offset=".15" stop-color="#fff"/><stop offset="1" stop-color="#fff"/>
        </linearGradient>
      </defs>
      <rect x="0" y="0" width="676" height="477" fill="url(#colFade)"/>
      <rect x="0" y="0" width="676" height="114" fill="#8e8e8e"/>
      <rect x="225" y="0" width="226" height="114" fill="var(--grey)"/>
      <circle cx="380" cy="100" r="90" fill="none" stroke="#bdbdbd" stroke-width=".8"/>
      <circle cx="610" cy="110" r="80" fill="none" stroke="#bdbdbd" stroke-width=".8"/>
      <circle cx="70" cy="46" r="100" fill="var(--green-dark)"/>
      <circle cx="66" cy="42" r="96" fill="var(--green)"/>
      <circle cx="62" cy="38" r="91" fill="#fff"/>
      <circle cx="60" cy="36" r="87" fill="url(#photoSoft)" role="img" aria-label="Close-up black and white photo of a newborn's feet"/>
      <rect x="255" y="370" width="176" height="104" rx="50" fill="url(#photoSoft)" role="img" aria-label="Black and white photo of a smiling baby under a white towel"/>
    </svg>

    <h2 class="abs inside-title" style="top:62px">LITTLE LANTERN</h2>

    <div class="abs col col--1">
      <div class="week">
        <h3 class="week__title">Week 1</h3>
        <p>GP Dr Helena Marsh will share information for Mum's own health after delivery. Topics include:</p>
        <ul class="bullets">
          <li>Vaccinations in pregnancy</li>
          <li>Bleeding, bladder and bowel after delivery</li>
          <li>Breastfeeding, engorgement and mastitis</li>
          <li>Bottle feeding</li>
          <li>Post-natal anxiety &amp; depression</li>
          <li>Intimacy and contraception</li>
        </ul>
      </div>
      <div class="week">
        <h3 class="week__title">Week 2</h3>
        <p><span class="session">Session 1</span> – Clinical Psychologist Dr Imogen Hale will discuss changes in relationships as couples become parents, gender roles in parenting and post-natal depression.</p>
        <p><span class="session">Session 2</span> – Physiotherapist Tessa Lowry will present advice for Mums regarding exercise during and after pregnancy, looking after the pelvic floor during and after pregnancy, and abdominal muscle separation management. She will also provide advice for promoting babies' neck strength and minimising the risk of flat spots on the head and encouraging gross motor skills in the first 6 months</p>
      </div>
    </div>

    <div class="abs col col--2">
      <div class="week">
        <h3 class="week__title">Week 3</h3>
        <p><span class="session">Session 1</span> – Dietician Nora Whitfield provides advice for Mums regarding healthy eating during pregnancy and lactation, normal weight gain during pregnancy and realistic weight loss after. She will also discuss the evidence regarding breastfeeding VS bottle-feeding, normal infant weight gain and introducing solids (including those with potential for allergy).</p>
        <p><span class="session">Session 2</span> – Paediatric Speech Pathologist Ruth Calder will share information about latching and breast-feeding troubles &amp; tongue tie, advice about dummies and finger-sucking, introducing solids &amp; feeding (including 'pouch' food), encouraging language development and current evidence about electronic devices impacting language development. strength and minimising the risk of flat spots on the head and encouraging gross motor skills in the first 6 months</p>
      </div>
    </div>

    <div class="abs col col--3">
      <div class="week">
        <h3 class="week__title">Week 4</h3>
        <p>GP Dr Helena Marsh will share advice about your babies' health in the first 6 months, including:</p>
        <ul class="bullets bullets--split">
          <li>Skin of newborns</li><li>Fever and infections</li>
          <li>Sleeping</li><li>Diarrhoea and constipation</li>
          <li>Crying</li><li>Teething</li>
          <li>Immunisations</li><li>Understanding a baby's signals</li>
        </ul>
      </div>
      <div class="week">
        <h3 class="week__title">Week 5</h3>
        <p><span class="session">Session 1</span> – Clinical Psychologist Dr Imogen Hale will share information about bonding &amp; attachment with your baby, how to promote their social &amp; emotional development and how to manage separation anxiety. She will also discuss positive parenting approaches.</p>
      </div>
      <div class="week">
        <h3 class="week__title">Week 6</h3>
        <p><span class="session">Session 1</span> – Secret Men's Business – a men-only session (including beer!) with a new father for frank discussion about the road ahead. Mums will do a shopping excursion with the GP &amp; Dietician to Greenway Grocers to look at baby products and food – the good and the bad!</p>
        <p><span class="session">Session 2</span> – Program review, reflection and evaluation and future session planning when baby is 6 months of age.</p>
      </div>
    </div>
  </section>

</div>
</body>
</html>
```